Meridale Partners Website

Meridale Partners (MP) provide Analytics & Enterprise Performance Management (EPM) advisory & consultancy services. We are passionate about data and making a difference for our clients by working in partnership with them, helping them on their journey to becoming an Meridale Partner. We deliver insights which give our clients a competitive edge and a much deeper understanding of their organisation.

We need a website which shows who we are, what we do and how we do it.

www.meridale-partners.example is our very basic website at the moment. We want to completely revamp it with a corporate look

```html
<!DOCTYPE html>
<html lang="en">
<head>
<meta charset="utf-8">
<title>Meridale Partners</title>
<link rel="stylesheet" href="https://fonts.googleapis.com/css2?family=Cormorant+Garamond:wght@400;500&family=Montserrat:wght@400;500;600;700&family=Roboto+Condensed:wght@300;400&display=swap">
<style>
:root{
  --navy:#2b566e;
  --navy-deep:#234a60;
  --hero-b:#2f5a73;
  --ink:#1d1d1d;
  --white:#ffffff;
  --pale:#f7f8fa;
  --line:rgba(255,255,255,.35);
}
*{margin:0;padding:0;box-sizing:border-box}
html,body{width:1200px;height:2652px;overflow:hidden}
body{font-family:"Roboto Condensed",sans-serif;color:var(--ink);background:var(--white);position:relative}
.serif{font-family:"Cormorant Garamond",serif;font-weight:500}
.abs{position:absolute}

/* header */
.site-header{position:absolute;top:0;left:0;width:1200px;height:97px;background:var(--white)}
.nav-link{position:absolute;top:40px;font-family:"Montserrat",sans-serif;font-weight:600;font-size:16px;color:var(--ink);text-decoration:none}
.nav-link.active{color:var(--navy)}
.brand{position:absolute;display:flex;align-items:center;gap:12px;font-family:"Montserrat",sans-serif;font-weight:700;letter-spacing:1px;text-transform:uppercase;line-height:1.05}
.brand-dot{border-radius:50%;flex:none}
.site-header .brand{left:514px;top:28px;color:var(--navy);font-size:16px}
.site-header .brand-dot{width:40px;height:40px;background:var(--navy)}
.search{position:absolute;left:1014px;top:42px}

/* hero */
.hero{position:absolute;top:97px;left:0;width:1200px;height:633px;background:linear-gradient(100deg,#4a7088 0%,var(--hero-b) 45%,#3e6780 75%,#2e5068 100%)}
.hero-welcome{left:144px;font-family:"Montserrat",sans-serif;font-weight:400;font-size:28px;color:var(--white)}
.hero-title{left:142px;font-size:74px;line-height:76px;color:var(--white);font-weight:400}
.hero-text{left:143px;width:330px;font-size:16.5px;line-height:27px;color:var(--white);font-weight:300}
.btn{position:absolute;height:38px;font-family:"Montserrat",sans-serif;font-weight:700;font-size:18px;display:flex;align-items:center;justify-content:center}
.btn-light{background:var(--white);color:var(--navy)}
.btn-dark{background:var(--navy);color:var(--white)}

/* who we are */
.who{position:absolute;top:730px;left:0;width:1200px;height:398px;background:var(--pale)}
.who-photo{position:absolute;left:0;top:0;width:540px;height:398px;background:linear-gradient(90deg,#b9c6d1 0%,#d9e0e7 50%,rgba(247,248,250,0) 100%)}
.section-title{position:absolute;left:0;width:1200px;text-align:center;font-size:48px}
.section-text{position:absolute;text-align:center;font-size:16.5px;line-height:27.3px;font-weight:300}

/* what we do */
.what{position:absolute;top:1128px;left:0;width:1200px;height:446px;background:var(--navy)}

/* how */
.card{position:absolute;width:450px;height:214px;background:var(--white);box-shadow:0 0 10px rgba(0,0,0,.07);display:flex;flex-direction:column;justify-content:center;align-items:center;text-align:center;font-family:"Montserrat",sans-serif}
.card h3{font-weight:700;font-size:23px;line-height:32px;color:var(--navy)}
.card p{font-size:16px;line-height:17px;margin-top:16px;color:var(--ink)}
.card.featured{background:linear-gradient(120deg,#5b7f96,#3e6580 60%,#365d77)}
.card.featured h3,.card.featured p{color:var(--white)}

/* footer */
.site-footer{position:absolute;top:2352px;left:0;width:1200px;height:300px;background:var(--navy);color:var(--white)}
.site-footer .brand{left:146px;top:78px;font-size:21px;color:var(--white)}
.site-footer .brand-dot{width:48px;height:48px;border:6px solid var(--white)}
.foot-about{left:146px;top:170px;width:245px;text-align:center;font-family:"Montserrat",sans-serif;font-size:12px;line-height:20px}
.vline{position:absolute;width:1px;background:var(--line)}
.foot-links{left:488px;top:54px;font-family:"Montserrat",sans-serif;font-size:12px;line-height:27.5px;list-style:none}
.contact-row{position:absolute;left:659px;display:flex;gap:8px;font-family:"Montserrat",sans-serif;font-size:12px;line-height:20px}
.contact-row svg{margin-top:4px;flex:none}
.tx-label{left:886px;top:84px;font-family:"Montserrat",sans-serif;font-size:12px}
.pay{position:absolute;top:109px;width:41px;height:24px;background:var(--white);border-radius:3px}
.copyright{left:460px;top:234px;font-family:"Montserrat",sans-serif;font-size:12px}
.social{position:absolute;top:235px;width:16px;height:16px;border-radius:50%;border:2px solid var(--white)}
</style>
</head>
<body>

<header class="site-header">
  <a class="nav-link active" style="left:215px" href="#">Home</a>
  <a class="nav-link" style="left:301px" href="#">Services</a>
  <div class="brand"><span class="brand-dot"></span><span>Meridale<br>Partners</span></div>
  <a class="nav-link" style="left:770px" href="#">About Us</a>
  <a class="nav-link" style="left:880px" href="#">Contact Us</a>
  <svg class="search" width="22" height="22" viewBox="0 0 22 22" fill="none" stroke="#1d1d1d" stroke-width="2"><circle cx="9" cy="9" r="7"/><path d="M14 14l6 6"/></svg>
</header>

<section class="hero" role="img" aria-label="Business colleagues working together in an office, tinted blue">
  <div class="abs hero-welcome" style="top:189px">Welcome to</div>
  <h1 class="abs hero-title serif" style="top:233px">Meridale<br>Partners</h1>
  <p class="abs hero-text" style="top:407px">Lorem Ipsum is simply dummy text of the printing and typesetting industry.</p>
  <div class="btn btn-light" style="left:143px;top:481px;width:145px">Get Started</div>
</section>

<section class="who">
  <div class="who-photo" role="img" aria-label="Team hands over charts and papers on a meeting table"></div>
  <h2 class="section-title serif" style="top:118px;color:#2c3e4b">Who We Are</h2>
  <p class="section-text" style="left:168px;top:182px;width:872px">Lorem Ipsum is simply dummy text of the printing and typesetting industry. Lorem Ipsum has been the industry's standard dummy text ever since the 1500s, when an unknown printer took a galley of type and scrambled it to make a type specimen book. It has survived not only five centuries, but also the leap into electronic typesetting, remaining essentially unchanged.</p>
</section>

<section class="what">
  <h2 class="section-title serif" style="top:80px;color:var(--white)">What We Do</h2>
  <p class="section-text" style="left:160px;top:146px;width:880px;color:var(--white)">Lorem Ipsum is simply dummy text of the printing and typesetting industry. Lorem Ipsum has been the industry's standard dummy text ever since the 1500s, when an unknown printer took a galley of type and scrambled it to make a type specimen book. It has survived not only five centuries, but also the leap into electronic typesetting, remaining essentially unchanged. It was popularised in the 1960s with the release of Typeline sheets containing Lorem Ipsum passages, and more recently with desktop publishing software like Pressform Layout including versions of Lorem Ipsum.</p>
  <div class="btn btn-light" style="left:530px;top:320px;width:145px">Learn More</div>
</section>

<section class="how">
  <h2 class="section-title serif" style="top:1634px;color:#2c3e4b">How We Do It</h2>
  <p class="section-text" style="left:160px;top:1700px;width:900px">Lorem Ipsum is simply dummy text of the printing and typesetting industry. Lorem Ipsum has been the industry's standard dummy text ever since the 1500s, when an unknown printer took a galley of type and scrambled it to make a type specimen book.</p>

  <div class="card featured" style="left:145px;top:1776px" role="img" aria-label="Businessman working at a laptop, tinted blue">
    <h3>Meridale Partners (MP)</h3>
    <p>Lorem Ipsum is simply dummy text of the printing<br>and typesetting industry.</p>
  </div>
  <div class="card" style="left:608px;top:1776px">
    <h3>Analytics &amp;<br>Enterprise Performance<br>Management (EPM)</h3>
    <p>Lorem Ipsum is simply dummy text of the printing<br>and typesetting industry.</p>
  </div>
  <div class="card" style="left:145px;top:2006px">
    <h3>Advisory Services</h3>
    <p>Lorem Ipsum is simply dummy text of the printing<br>and typesetting industry.</p>
  </div>
  <div class="card" style="left:608px;top:2006px">
    <h3>Consultancy Services</h3>
    <p>Lorem Ipsum is simply dummy text of the printing<br>and typesetting industry.</p>
  </div>

  <div class="btn btn-dark" style="left:531px;top:2250px;width:145px">View More</div>
</section>

<footer class="site-footer">
  <div class="brand"><span class="brand-dot"></span><span>Meridale<br>Partners</span></div>
  <p class="abs foot-about">Lorem Ipsum is simply dummy text of the printing and typesetting industry.</p>

  <div class="vline" style="left:429px;top:38px;height:240px"></div>
  <div class="vline" style="left:607px;top:38px;height:145px"></div>
  <div class="vline" style="left:842px;top:38px;height:145px"></div>
  <div class="abs" style="left:429px;top:208px;width:628px;height:1px;background:var(--line)"></div>

  <ul class="abs foot-links">
    <li>Home</li><li>About Us</li><li>Services</li><li>Contact Us</li>
  </ul>

  <div class="contact-row" style="top:54px">
    <svg width="10" height="12" viewBox="0 0 10 12" fill="#fff"><path d="M5 0a4.5 4.5 0 0 0-4.5 4.5C.5 8 5 12 5 12s4.5-4 4.5-7.5A4.5 4.5 0 0 0 5 0zm0 6.3a1.8 1.8 0 1 1 0-3.6 1.8 1.8 0 0 1 0 3.6z"/></svg>
    <span>#1, Harbour Lane,<br>Quay Road - 52790</span>
  </div>
  <div class="contact-row" style="top:104px">
    <svg width="12" height="12" viewBox="0 0 12 12" fill="none" stroke="#fff" stroke-width="1.2"><path d="M2.5 1h2l1 3-1.5 1a6 6 0 0 0 3 3l1-1.5 3 1v2a1 1 0 0 1-1 1A10 10 0 0 1 1.5 2a1 1 0 0 1 1-1z"/></svg>
    <span>+1 (55) 555 0142</span>
  </div>
  <div class="contact-row" style="top:135px">
    <svg width="12" height="10" viewBox="0 0 12 10" fill="#fff"><path d="M0 1h12v8H0z"/><path d="M0 1l6 4 6-4" stroke="#2b566e" fill="none"/></svg>
    <span>hello@meridale.example</span>
  </div>

  <div class="abs tx-label">Transaction Details</div>
  <div class="pay" style="left:876px"></div>
  <div class="pay" style="left:925px"></div>
  <div class="pay" style="left:974px"></div>

  <div class="abs copyright">© copyrights 2022 Meridale Partners | &nbsp;All Rights Reserved</div>
  <div class="social" style="left:928px"></div>
  <div class="social" style="left:962px"></div>
  <div class="social" style="left:996px"></div>
</footer>

</body>
</html>
```